Detail Shop Business card design

i need a business card design for my new detailing company called 'Brisk's Polish Works'. i want an all black and white design . simple, direct and to the point. i want the designer to choose a fitting font to match the logothe front should have logo, address, phone and email and the back side should have a slogan and text indicating that we offer services on anything including cars, trucks, motorcycles and RVs. slogan will read "we take pride in your ride"
maybe also very small on the back side the IG icon with Brisks_Polish_Works

phone 208.417.6352
address 3847 E Larkin Ave
Spokane WA 99214
email: BrisksPolish@mailvexo.com

Target Market(s)

all ages , auto enthusiasts

Industry/Entity Type

Automotive

Contact Information for Business Card

the front should have logo, address, phone and email and the back side should have a slogan and text indicating that we offer services on anything including cars, trucks, motorcycles and RVs. slogan will read "we take pride in your ride"

phone 208.417.6352
address 3847 E Larkin Ave
Spokane WA 99214

Colors
000000
ffffff

Requirements
Must have
• bold font and very simple design with good spacing
Nice to have
• anything creative from the designer indicating we service any types of vehicles
Should not have
• any colors ,

```html
<!DOCTYPE html>
<html lang="en">
<head>
<meta charset="utf-8">
<title>Brisk's Polish Works – Business Card</title>
<link rel="stylesheet" href="https://fonts.googleapis.com/css2?family=Lato:wght@400;700;900&display=swap">
<style>
  :root {
    --backdrop: #3a3431;
    --card: #0d0d0d;
    --ink: #ffffff;
    --ink-soft: #d9d9d9;
    --rule: #3c3c3c;
  }
  * { box-sizing: border-box; margin: 0; padding: 0; }
  html, body { width: 1200px; height: 844px; overflow: hidden; }
  body {
    background: var(--backdrop);
    font-family: "Lato", sans-serif;
    color: var(--ink);
    display: flex;
    align-items: center;
    justify-content: center;
    gap: 60px;
  }
  .card {
    position: relative;
    width: 520px;
    height: 297px;
    background: var(--card);
    box-shadow: 0 18px 40px rgba(0,0,0,.45);
  }
  .brand {
    position: absolute;
    left: 34px;
    top: 0;
    bottom: 0;
    width: 230px;
    display: flex;
    align-items: center;
    justify-content: center;
    gap: 12px;
  }
  .brand-dot {
    width: 18px;
    height: 18px;
    border-radius: 50%;
    background: var(--ink);
    flex: none;
  }
  .brand-name {
    font-weight: 900;
    font-size: 26px;
    line-height: 1.1;
    text-transform: uppercase;
    letter-spacing: .5px;
    color: var(--ink);
  }
  .divider {
    position: absolute;
    left: 282px;
    top: 60px;
    width: 1px;
    height: 150px;
    background: var(--rule);
  }
  .details {
    position: absolute;
    left: 304px;
    right: 20px;
    font-size: 13.5px;
    line-height: 1.45;
    color: var(--ink-soft);
  }
  .front .details { top: 96px; }
  .contact-line { display: flex; align-items: center; gap: 6px; }
  .contact-line svg { width: 12px; height: 12px; flex: none; fill: var(--ink); }
  .address { margin-top: 18px; }
  .back .details { top: 62px; }
  .services { font-size: 13px; line-height: 1.5; }
  .social { margin-top: 20px; display: flex; align-items: center; gap: 7px; font-size: 12.5px; }
  .social-dot { width: 12px; height: 12px; border-radius: 50%; background: var(--ink); flex: none; }
  .slogan {
    position: absolute;
    right: 28px;
    bottom: 44px;
    font-weight: 700;
    font-size: 14px;
    letter-spacing: .4px;
    text-transform: uppercase;
    color: var(--ink);
  }
</style>
</head>
<body>
  <section class="card front">
    <div class="brand">
      <span class="brand-dot"></span>
      <span class="brand-name">Brisk's Polish Works</span>
    </div>
    <div class="divider"></div>
    <div class="details">
      <p class="contact-line">
        <svg viewBox="0 0 24 24" aria-hidden="true"><path d="M6.6 10.8a15 15 0 0 0 6.6 6.6l2.2-2.2a1 1 0 0 1 1-.25 11.4 11.4 0 0 0 3.6.57 1 1 0 0 1 1 1V20a1 1 0 0 1-1 1A17 17 0 0 1 3 4a1 1 0 0 1 1-1h3.5a1 1 0 0 1 1 1c0 1.25.2 2.46.57 3.6a1 1 0 0 1-.25 1z"/></svg>
        208.417.6352
      </p>
      <p class="contact-line">
        <svg viewBox="0 0 24 24" aria-hidden="true"><path d="M2 5h20v14H2zm2 2v.5l8 5 8-5V7zm0 2.8V17h16V9.8l-8 5z"/></svg>
        BrisksPolish@mailvexo.com
      </p>
      <p class="address">3847 E Larkin Ave<br>Spokane WA 99214</p>
    </div>
  </section>

  <section class="card back">
    <div class="brand">
      <span class="brand-dot"></span>
      <span class="brand-name">Brisk's Polish Works</span>
    </div>
    <div class="divider"></div>
    <div class="details">
      <p class="services">We offer services on anything including cars, trucks, motorcycles and RVs.</p>
      <p class="social"><span class="social-dot"></span>Brisks_Polish_Works</p>
    </div>
    <p class="slogan">We take pride in your ride</p>
  </section>
</body>
</html>
```